Anzeigengestaltung für Fliesenlegermeister
Zielgruppe
Ich bin ein Fliesenlegermeister und möchte mich selbstständig machen, ich saniere Bäder, Böden mit Fliesen, Fliesenspiegel und ich möchte eine Anzeige in den regionalen Zeitungen machen. Ich spreche alle Altersklassen mit Bädern für Sanierungen, Bodenfliesen und Neubauten an. Reparatur und Silikonarbeiten sowie Trockenbauarbeiten am eigenen Heim .
Aufgabenstellung
Ich möchte gern meine Kontaktdaten und die Farben vom Logo wieder finden,
als Beispiel habe ich meine aktuelle Visitenkarte beigefügt Dort finden sich die Kontaktdaten. Meine Arbeiten sind insbesondere :
Fliesenverlegung
Badsanierung
barrierefreie Bäder
Reparaturarbeiten
Silikonarbeiten
Trockenbau
Ob nun genau alle 6 Punkte in der Anzeige angezeigt werden soll bin ich mir nicht sicher oder ob nur 4 Beschreibungen reichen, damit es nicht zu viel wird.

```html
<!DOCTYPE html>
<html lang="de">
<head>
<meta charset="utf-8">
<title>Anzeige Fliesenlegermeister Jonas Terhalm</title>
<link rel="stylesheet" href="https://fonts.googleapis.com/css2?family=Roboto:wght@400;500;700&family=Rajdhani:wght@600&display=swap">
<style>
  :root {
    --brand-blue: #0b539b;
    --charcoal: #4a4a4c;
    --rule-grey: #d0d0d2;
    --paper: #ffffff;
    --tile-light: #e8c2a0;
    --tile-dark: #c99570;
  }
  html, body {
    margin: 0;
    padding: 0;
    width: 1200px;
    height: 1200px;
    overflow: hidden;
    background: var(--paper);
  }
  .canvas { display: block; width: 1200px; height: 1200px; }
  .ad-frame { fill: var(--paper); stroke: var(--charcoal); stroke-width: 5; }
  .guide-line { fill: none; stroke: var(--rule-grey); stroke-width: 14; stroke-linejoin: miter; }
  .headline-box { fill: var(--paper); stroke: var(--rule-grey); stroke-width: 14; }
  .headline { font-family: "Rajdhani", sans-serif; font-weight: 600; font-size: 40px; fill: var(--charcoal); letter-spacing: 1px; }
  .service-bullet { fill: var(--brand-blue); }
  .service { font-family: "Roboto", sans-serif; font-weight: 500; font-size: 41px; fill: var(--charcoal); }
  .contact-bar { fill: var(--charcoal); }
  .phone-number { font-family: "Roboto", sans-serif; font-weight: 700; font-size: 48px; fill: var(--paper); }
  .contact-icon { fill: none; stroke: var(--paper); stroke-width: 2.5; stroke-linecap: round; stroke-linejoin: round; }
  .address-icon { fill: none; stroke: var(--charcoal); stroke-width: 2.5; }
  .address { font-family: "Roboto", sans-serif; font-weight: 400; font-size: 31px; fill: var(--charcoal); }
  .brand-mark { fill: var(--brand-blue); }
  .brand-name { font-family: "Roboto", sans-serif; font-weight: 700; font-size: 50px; fill: var(--brand-blue); letter-spacing: 1px; }
  .email { font-family: "Roboto", sans-serif; font-weight: 400; font-size: 42px; fill: var(--charcoal); }
</style>
</head>
<body>
<svg class="canvas" viewBox="0 0 1736 1736" xmlns="http://www.w3.org/2000/svg">
  <defs>
    <linearGradient id="tile-tones" x1="0" y1="0" x2="1" y2="1">
      <stop offset="0" stop-color="var(--tile-light)"/>
      <stop offset="1" stop-color="var(--tile-dark)"/>
    </linearGradient>
  </defs>

  <rect class="ad-frame" x="425" y="375" width="886" height="985"/>

  <g role="img" aria-label="Foto: Hand markiert mit Bleistift und Zollstock eine Fliese zum Zuschneiden">
    <polygon points="428,378 1308,378 1308,580 870,612 790,580 428,580" fill="url(#tile-tones)"/>
  </g>

  <path class="guide-line" d="M790,585 L868,625 L868,1052 L665,1254 L428,1254"/>

  <rect class="headline-box" x="587" y="669" width="562" height="111" rx="22"/>
  <text class="headline" x="862" y="715" text-anchor="middle">PROFESSIONELLER</text>
  <text class="headline" x="868" y="759" text-anchor="middle">FLIESENLEGERMEISTER</text>

  <g class="services">
    <path class="service-bullet" d="M457,845 l13,13 l-13,13 l-13,-13z"/>
    <text class="service" x="490" y="873">Fliesenverlegung</text>
    <path class="service-bullet" d="M457,895 l13,13 l-13,13 l-13,-13z"/>
    <text class="service" x="490" y="923">Badsanierung</text>
    <path class="service-bullet" d="M457,945 l13,13 l-13,13 l-13,-13z"/>
    <text class="service" x="490" y="973">barrierefreie Bäder</text>
    <path class="service-bullet" d="M457,995 l13,13 l-13,13 l-13,-13z"/>
    <text class="service" x="490" y="1023">Reparaturarbeiten</text>
    <path class="service-bullet" d="M457,1045 l13,13 l-13,13 l-13,-13z"/>
    <text class="service" x="490" y="1073">Silikonarbeiten</text>
    <path class="service-bullet" d="M457,1095 l13,13 l-13,13 l-13,-13z"/>
    <text class="service" x="490" y="1124">Trockenbau</text>
  </g>

  <rect class="contact-bar" x="876" y="843" width="432" height="82"/>
  <path class="contact-icon" d="M893,870 c-6,6 -4,18 6,28 c10,10 22,12 28,6 l-8,-9 l-6,4 c-5,-2 -13,-10 -15,-15 l4,-6 z M912,866 a14,14 0 0 1 12,12 M912,858 a22,22 0 0 1 20,20"/>
  <text class="phone-number" x="1290" y="901" text-anchor="end">05321/4478210</text>

  <rect class="contact-bar" x="876" y="933" width="432" height="82"/>
  <rect class="contact-icon" x="886" y="950" width="32" height="50" rx="4"/>
  <path class="contact-icon" d="M886,990 h32 M899,956 h6"/>
  <circle class="contact-icon" cx="902" cy="995" r="2"/>
  <text class="phone-number" x="1290" y="991" text-anchor="end">01762945318</text>

  <path class="address-icon" d="M900,1092 c-12,-18 -16,-26 -16,-34 a16,16 0 0 1 32,0 c0,8 -4,16 -16,34 z"/>
  <circle class="address-icon" cx="900" cy="1058" r="6"/>
  <text class="address" x="928" y="1069">Ahornweg 12, 38126</text>
  <text class="address" x="928" y="1107">Feldheim</text>

  <rect class="brand-mark" x="822" y="1172" width="34" height="34"/>
  <text class="brand-name" x="1292" y="1207" text-anchor="end">JONAS TERHALM</text>

  <text class="email" x="868" y="1323" text-anchor="middle">info@fliesen-terhalm.de</text>
</svg>
</body>
</html>
```